Brightway Haul & Upkeep Services, are a company that offers a 'one stop shop' pre-move clean up a

I have already selected a logo which I would like on the front of the business cards along with phone numbers, web address and email which are:
0487650392
www.brightwayhaul.com.au
brightwayhaulandupkeep@mailbox.example

On the back of the card I would like to list some of the types of service we offer (clean - move - repairs/maintenance) which are:
CLEAN - windows, gutters, solar panels, driveways/paths, carpets.
MOVE - Small/medium size house/office moves, large item pick-up & delivery, yard clean-up and removal.
General maintenance and repairs.

I would like the blue logo on a gray background.

Thanks

```html
<!DOCTYPE html>
<html lang="en">
<head>
<meta charset="utf-8">
<title>Brightway Haul &amp; Upkeep Services – Business Card</title>
<link href="https://fonts.googleapis.com/css2?family=Open+Sans:wght@400;600;700;800&display=swap" rel="stylesheet">
<style>
  :root {
    --backdrop: #d9d4ce;
    --card-light: #eeeeee;
    --card-mid: #cfd0d1;
    --card-dark: #b5b6b8;
    --brand-blue: #2a6fbd;
    --band-blue: #1f6bbd;
    --ink: #222226;
    --white: #ffffff;
    --faint: rgba(120, 150, 190, 0.22);
  }
  * { box-sizing: border-box; margin: 0; padding: 0; }
  html, body { width: 1200px; height: 382px; overflow: hidden; }
  body {
    background: var(--backdrop);
    font-family: "Open Sans", Arial, sans-serif;
    position: relative;
  }
  .card {
    position: absolute;
    top: 27px;
    width: 538px;
    height: 307px;
    overflow: hidden;
    box-shadow: 0 2px 6px rgba(0,0,0,0.35);
  }
  .card--front {
    left: 45px;
    background: radial-gradient(ellipse at 55% 35%, var(--card-light) 0%, var(--card-mid) 60%, var(--card-dark) 100%);
  }
  .card--back {
    left: 628px;
    width: 537px;
    background: radial-gradient(ellipse at 40% 20%, #dcdcdd 0%, #c4c5c7 55%, #a9aaac 100%);
  }

  /* Front */
  .brand-name {
    position: absolute;
    top: 78px;
    left: 0;
    width: 100%;
    text-align: center;
    color: var(--brand-blue);
    font-weight: 800;
    text-transform: uppercase;
    line-height: 1.1;
  }
  .brand-name__main { display: block; font-size: 36px; letter-spacing: 0.3px; }
  .brand-name__sub { display: block; font-size: 18px; margin-top: 6px; }
  .contact-list {
    position: absolute;
    top: 173px;
    left: 0;
    width: 100%;
    list-style: none;
    text-align: center;
    color: var(--ink);
    font-size: 14.5px;
  }
  .contact-list li { line-height: 23px; }
  .contact-list svg { width: 11px; height: 11px; vertical-align: -1px; margin-right: 5px; }
  .contact-band {
    position: absolute;
    left: 0;
    bottom: 0;
    width: 100%;
    height: 58px;
    background: var(--band-blue);
  }
  .phone {
    position: absolute;
    left: 62px;
    top: 18px;
    color: var(--white);
    font-size: 18px;
    display: flex;
    align-items: center;
    gap: 6px;
  }
  .phone svg { width: 15px; height: 15px; }

  /* Back */
  .services__title {
    position: absolute;
    left: 25px;
    top: 36px;
    color: var(--white);
    font-size: 25px;
    font-weight: 700;
  }
  .services__list {
    position: absolute;
    left: 25px;
    top: 82px;
    color: var(--ink);
    font-size: 19px;
    font-weight: 600;
    line-height: 34px;
  }
  .services__row { display: flex; gap: 18px; }
  .services__item::before {
    content: "•";
    color: var(--brand-blue);
    margin-right: 7px;
  }
  .faint-name {
    position: absolute;
    left: 0;
    top: 190px;
    width: 100%;
    text-align: center;
    color: var(--faint);
    font-weight: 800;
    text-transform: uppercase;
    line-height: 1.1;
  }
  .faint-name__main { display: block; font-size: 52px; }
  .faint-name__sub { display: block; font-size: 27px; margin-top: 8px; }
</style>
</head>
<body>

<section class="card card--front" aria-label="Business card front">
  <h1 class="brand-name">
    <span class="brand-name__main">Brightway Haul</span>
    <span class="brand-name__sub">&amp; Upkeep Services</span>
  </h1>

  <ul class="contact-list">
    <li>
      <svg viewBox="0 0 12 12" aria-hidden="true"><circle cx="6" cy="6" r="5.3" fill="none" stroke="#2a6fbd" stroke-width="1.3"/><path d="M0.8 6h10.4M6 0.8c-2.4 2.8-2.4 7.6 0 10.4M6 0.8c2.4 2.8 2.4 7.6 0 10.4" fill="none" stroke="#2a6fbd" stroke-width="1"/></svg>www.brightwayhaul.com.au
    </li>
    <li>
      <svg viewBox="0 0 12 12" aria-hidden="true"><rect x="0.5" y="2.5" width="11" height="7.5" fill="#2a6fbd"/><path d="M0.5 2.5L6 7l5.5-4.5" fill="none" stroke="#ffffff" stroke-width="1"/></svg>brightwayhaulandupkeep@mailbox.example
    </li>
  </ul>

  <div class="contact-band">
    <div class="phone">
      <svg viewBox="0 0 16 16" aria-hidden="true"><circle cx="8" cy="8" r="7" fill="none" stroke="#ffffff" stroke-width="1.3"/><path d="M5.2 4.5c.5-.4 1-.3 1.3.2l.6 1.1c.2.4 0 .8-.3 1l-.4.3c.4 1 1.1 1.8 2.1 2.3l.3-.4c.3-.3.7-.4 1-.2l1.1.6c.5.3.5.9.1 1.3-1.2 1.2-3.3.4-4.7-1.1S4 5.6 5.2 4.5z" fill="#ffffff"/></svg>
      <span>0487650392</span>
    </div>
  </div>
</section>

<section class="card card--back" aria-label="Business card back">
  <h2 class="services__title">Services we offer</h2>
  <div class="services__list">
    <div class="services__row">
      <span class="services__item">Clean</span>
      <span class="services__item">Move</span>
    </div>
    <div class="services__row">
      <span class="services__item">General Maintenance And Repairs.</span>
    </div>
  </div>
  <div class="faint-name" aria-hidden="true">
    <span class="faint-name__main">Brightway Haul</span>
    <span class="faint-name__sub">&amp; Upkeep Services</span>
  </div>
</section>

</body>
</html>
```